Merrisol. Sunless Tanning Mousse Label

I'm looking for a label creation for a new brand of sunless tanning solutions. They are in 6.7oz bottles (template attached).

For the front of the bottle (see template) I would like an abstract multi coloured design taking up just over half the top of the bottle (approx 60%) and going around the design (this is similar to the design inspiration attached). I would this design to use the attached colour palette of pinks. It can be swirls, drips, squares, lines, whatever you think will look good.

The logo will then be over top of that abstract design in the upper 1/3, in the colour #3fe0d0

Under the abstract design the following text:

Amber Hush (Larger text)
Violet Base (2nd heading)
1 Hour Sunless Mousse (Sub text)
The No Orange Guarantee! (Sub text)
Vegan Formula (sub text)

The sub texts for above can be fun, have coloured background, different fonts, whatever looks good and is sill fun.

Towards the bottom of the front of bottle we require the sizing information:

200ml 6.7 Fl Oz

On the left side of the front (so in the template the middle smaller section) I would like the phrase "You ain't gotta get ready if you stay ready" Could you please make this as a separate little quote, with a fun design to it. It's like a little hidden gem on the side of the bottle.

On the back of the bottle for now can you please start towards the top with:

Amber Hush Mousse (larger)
Violet base (second heading)
Deep Mediterranean Inspired Tan (second heading)
Easy to Apply & Streak Free
Vegan friendly & 100% natural DHA tan actives

Under this I require approx 1.5" of Lorem Ipsum for now which will take the place of directions for using the product.

Under that in small writing can we include "Warning: This product does not contain a sunscreen and will not protect against sunburn. For external use only. If skin irritation occurs, discontinue use. Carry out a patch test 24 hours prior to full body use. Store below 25(degrees sign)C."

At the bottom is the smallest yet still legible writing, can we include the ingredients that are listed below.

Target Market(s)

Females 24-35 who take care of themselves and always want to look good. It's a youthful fun product.

Requirements
Must have
• Bright colours, and just screams FUN and youthful.

Ingredients must be listed on the back. They dont' need to take up more than an inch in height, less if possible.
*******************************************

INGREDIENTS: Water (Aqua), Propylene Glycol, Dihydroxyacetone, Peg-6 Caprylic/Capric Glycerides, Dihydroxypropyl Peg-5 Linoleammonium Chloride, Peg-7 Glyceryl Cocoate, Caramel,
Phenoxyethanol, Caprylyl Glycol, Potassium Sorbate, Hexylene Glycol, Glycerin, Helianthus Annuus (Sunflower) Seed Oil, Beta Vulgaris (Beet) Root Extract, Panthenol, Solanum Lycopersicum
(Tomato) Fruit Extract, Vaccinium Macrocarpon (Cranberry) Fruit Extract, L-ascorbic Acid (Vitamin C), Tocopheryl Acetate (Vitamin E), Theobroma Cacao (Cocoa) Seed Butter, Rosa Canina (Rose Hip)
Fruit Oil, Glycine Soja (Soybean) Oil, Cucumis Sativus (Cucumber) Fruit Extract, Blue 1 (CI 42090), Red 40 (CI 16035), Yellow 6 (CI 15985), Green 5 (CI 61570), Yellow 5 (CI 19140), Red 33 (CI 17200)

*****************************
Nice to have
• Several options to choose from, some can include a gradient into geometric shapes, rather than solid colour. Experiment
Should not have
• Do not want it to look medical.
Want colours to stay in the same pink family for the abstract design - can use white also.

```html
<!DOCTYPE html>
<html lang="en">
<head>
<meta charset="utf-8">
<title>Merrisol – Amber Hush Mousse Label</title>
<link href="https://fonts.googleapis.com/css2?family=Baloo+2:wght@400;500;600&family=Poppins:wght@500;700&family=Roboto+Condensed:wght@400;700&display=swap" rel="stylesheet">
<style>
  :root{
    --stage:#f752a8;
    --sheet:#ffffff;
    --berry:#b0357a;
    --violet:#a8128f;
    --magenta:#b0128f;
    --hot-pink:#e8157a;
    --soft-pink:#f45aa8;
    --tag-pink:#e0157a;
    --cut-line:#1a1a1a;
  }
  *{margin:0;padding:0;box-sizing:border-box}
  html,body{width:778px;height:1200px;overflow:hidden;background:var(--stage)}
  .sheet{position:absolute;left:13px;top:283px;width:792px;height:666px;background:var(--sheet);transform:scale(.95);transform-origin:0 0}
  .sheet-marks{position:absolute;inset:0}
  .label{position:absolute;left:26px;top:25px;width:740px;height:617px;overflow:hidden;background:var(--sheet)}
  .label-art{position:absolute;inset:0}
  .back-panel,.front-panel{position:absolute;text-align:center}
  .back-panel{left:30px;top:0;width:265px;height:617px}
  .front-panel{left:395px;top:0;width:266px;height:617px}
  .title{font-family:"Baloo 2",sans-serif;font-weight:600;color:var(--berry);line-height:.95}
  .back-panel .title{position:absolute;left:0;right:0;top:126px;font-size:32px}
  .base{font-family:"Baloo 2",sans-serif;font-weight:600;color:var(--violet)}
  .back-panel .base{position:absolute;left:0;right:0;top:222px;font-size:21px}
  .tan-style{position:absolute;left:0;right:0;top:274px;font-family:"Baloo 2",sans-serif;font-weight:400;font-size:17px;line-height:1.05;color:var(--berry)}
  .claims{position:absolute;left:0;right:0;top:324px;list-style:none;font-family:"Baloo 2",sans-serif;font-size:11px;line-height:1.05;color:var(--violet)}
  .claims li{display:flex;justify-content:center;align-items:center;gap:4px;margin-bottom:2px}
  .claims svg{flex:none}
  .info{position:absolute;left:10px;width:245px;text-align:justify;font-family:"Roboto Condensed",sans-serif;font-size:6px;line-height:1.3}
  .info-head{display:inline-block;background:var(--tag-pink);color:#fff;font-weight:700;font-size:7.5px;padding:1px 4px;margin-bottom:2px}
  .info p{color:var(--violet)}
  .info.warning p,.info.ingredients p{color:var(--magenta)}
  .info.using{top:376px}
  .info.warning{top:452px}
  .info.ingredients{top:501px}
  .side-quote{position:absolute;left:336px;top:26px;writing-mode:vertical-rl;font-family:"Poppins",sans-serif;font-weight:700;font-size:9.5px;letter-spacing:.2px;color:#fff;text-transform:uppercase}
  .brand{position:absolute;left:0;right:0;top:118px;font-family:"Poppins",sans-serif;font-weight:500;font-size:46px;letter-spacing:1px;color:#fff}
  .front-panel .title{position:absolute;left:0;right:0;top:410px;font-size:38px}
  .front-panel .base{position:absolute;left:0;right:0;top:470px;font-size:24px}
  .tag{position:absolute;height:14px;font-family:"Poppins",sans-serif;font-weight:500;font-size:9px;line-height:14px;color:#fff;text-align:center}
  .tag.sunless{left:30px;top:520px;width:161px;background:var(--soft-pink)}
  .tag.no-orange{left:55px;top:534px;width:180px;background:var(--berry)}
  .tag.vegan{left:30px;top:549px;width:149px;background:var(--violet)}
  .size{position:absolute;left:0;right:0;top:585px;font-family:"Baloo 2",sans-serif;font-size:12px;color:var(--berry)}
</style>
</head>
<body>
<div class="sheet">
  <svg class="sheet-marks" width="792" height="666" viewBox="0 0 792 666">
    <g stroke="var(--cut-line)" stroke-width="1">
      <line x1="0" y1="25" x2="792" y2="25"/>
      <line x1="0" y1="642" x2="792" y2="642"/>
      <line x1="26" y1="0" x2="26" y2="666"/>
      <line x1="766" y1="0" x2="766" y2="666"/>
    </g>
  </svg>
  <div class="label">
    <svg class="label-art" width="740" height="617" viewBox="0 0 740 617">
      <defs>
        <linearGradient id="pinkGrad" x1="0" y1="0" x2="1" y2="1">
          <stop offset="0" stop-color="var(--magenta)"/>
          <stop offset=".5" stop-color="var(--hot-pink)"/>
          <stop offset="1" stop-color="var(--magenta)"/>
        </linearGradient>
      </defs>
      <path role="img" aria-label="Abstract pattern of diagonal interlocking pink and violet bars" fill="url(#pinkGrad)"
        d="M0 0H740V330L715 310L690 335L665 315L640 370L610 345L580 380L545 355L510 385L470 360L440 385L410 355L395 345L370 335L345 360L320 335L300 375L280 385H0Z"/>
      <polygon fill="#fff" points="60,100 90,83 120,100 150,83 180,100 210,83 240,100 260,95 280,120 265,150 285,180 270,210 285,240 270,270 285,300 270,330 280,386 40,386 50,350 35,320 50,290 35,260 50,230 35,200 50,170 35,140 55,115"/>
      <g fill="none" stroke="var(--cut-line)" stroke-width="1" stroke-dasharray="5 3">
        <rect x="8" y="8" width="724" height="598"/>
        <line x1="30" y1="8" x2="30" y2="606"/>
        <line x1="295" y1="8" x2="295" y2="606"/>
        <line x1="395" y1="8" x2="395" y2="606"/>
        <line x1="661" y1="8" x2="661" y2="606"/>
      </g>
    </svg>

    <section class="back-panel">
      <h2 class="title">Amber Hush<br>Mousse</h2>
      <p class="base">Violet Base</p>
      <p class="tan-style">Deep Mediterranean<br>Inspired Tan</p>
      <ul class="claims">
        <li><svg width="11" height="11" viewBox="0 0 12 12"><circle cx="6" cy="6" r="5" fill="none" stroke="var(--violet)" stroke-width="1.4"/><path d="M3.5 6l2 2 4-5" fill="none" stroke="var(--violet)" stroke-width="1.6"/></svg>Easy to Apply &amp; Streak Free</li>
        <li><svg width="11" height="11" viewBox="0 0 12 12"><circle cx="6" cy="6" r="5" fill="none" stroke="var(--violet)" stroke-width="1.4"/><path d="M3.5 6l2 2 4-5" fill="none" stroke="var(--violet)" stroke-width="1.6"/></svg><span>Vegan friendly &amp; 100%<br>natural DHA tan actives</span></li>
      </ul>
      <div class="info using">
        <span class="info-head">USING:</span>
        <p>Lorem ipsum dolor sit amet, consectetuer adipiscing elit. Maecenas porttitor congue massa. Fusce posuere, magna sed pulvinar ultricies, purus lectus malesuada libero, sit amet commodo magna eros quis urna. Nunc viverra imperdiet enim. Fusce est. Vivamus a tellus. Pellentesque habitant morbi tristique senectus et netus et malesuada fames ac turpis egestas. Proin pharetra nonummy pede. Mauris et orci.</p>
      </div>
      <div class="info warning">
        <span class="info-head">WARNING:</span>
        <p>This product does not contain a sunscreen and will not protect against sunburn. For external use only. If skin irritation occurs, discontinue use. Carry out a patch test 24 hours prior to full body use. Store below 25°C.</p>
      </div>
      <div class="info ingredients">
        <span class="info-head">INGREDIENTS:</span>
        <p>Water (Aqua), Propylene Glycol, Dihydroxyacetone, Peg-6 Caprylic/Capric Glycerides, Dihydroxypropyl Peg-5 Linoleammonium Chloride, Peg-7 Glyceryl Cocoate, Caramel, Phenoxyethanol, Caprylyl Glycol, Potassium Sorbate, Hexylene Glycol, Glycerin, Helianthus Annuus (Sunflower) Seed Oil, Beta Vulgaris (Beet) Root Extract, Panthenol, Solanum Lycopersicum (Tomato) Fruit Extract, Vaccinium Macrocarpon (Cranberry) Fruit Extract, L-ascorbic Acid (Vitamin C), Tocopheryl Acetate (Vitamin E), Theobroma Cacao (Cocoa) Seed Butter, Rosa Canina (Rose Hip) Fruit Oil, Glycine Soja (Soybean) Oil, Cucumis Sativus (Cucumber) Fruit Extract, Blue 1 (CI 42090), Red 40 (CI 16035), Yellow 6 (CI 15985), Green 5 (CI 61570), Yellow 5 (CI 19140), Red 33 (CI 17200).</p>
      </div>
    </section>

    <p class="side-quote">You ain't gotta get ready if you stay ready</p>

    <section class="front-panel">
      <p class="brand">Merrisol</p>
      <h1 class="title">Amber Hush</h1>
      <p class="base">Violet Base</p>
      <span class="tag sunless">1 Hour Sunless Mousse</span>
      <span class="tag no-orange">The No Orange Guarantee!</span>
      <span class="tag vegan">Vegan Formula</span>
      <p class="size">200ml 6.7 Fl Oz</p>
    </section>
  </div>
</div>
</body>
</html>
```